Birch And Harbor Website A Website design for book editing

A website design for book editing

Our proofreading, editing and manuscript review packages are specifically tailored to help you publish the best possible version of your story.

NEED HELP PUBLISHING A BESTSELLER?

If you’re looking for professional book editing services from senior publishing industry insiders, look no further. Besides editing, we can also answer all your publishing questions and get you started building your author platform.

OUR SERVICES

We've carefully structured our packages to maximize value for every budget.

PRICING

$.02
PER WORD
Proofreading
Line Edit (Copy-editing)
Fix spelling and grammar
Sales copy/summary revision

$.04
PER WORD
Proofreading
Line Edit (Copy-editing)
Fix spelling and grammar
Organization and content
Plot and pacing
Manuscript Review

$.06
PER WORD
Proofreading
Line Edit (Copy-editing)
Fix spelling and grammar
Organization and content
Plot and pacing
Manuscript Review
Formatting (print and ebook)
Pre-publication proofread

OUR PROCESS

Send us a sample of your book. Our caffeine-fueled, eagle-eyed editors will go through it and then email you with their comments and suggestions. You can ask them any questions you want. They will look for…

Typos and grammatical errors.
Spelling and word choice issues
Punctuation and style
Word choice, clarity and flow.
Sentence structure and craft
If your writing is already clean, then they’ll discuss bigger picture things with you, like theme, concept, purpose, audience, potential market and branding (including title, subtitle, and tagline or elevator pitch).

Once you feel comfortable and confident in an editor’s expertise, skill and knowledge, and are ready to move ahead, we’ll send an invoice for the first half of the total word count so the editor can get started. We’ll charge the rest when the project is close to completion.

Target Market(s)

Authors

Industry/Entity Type

Book Publisher

Coding

Coded - Design and coding required

Number of Pages Required

1 page

Requirements
Must have
• OUR SERVICES
• We've carefully structured our packages to maximize value for every budget.
• PRICING
• $.02
• PER WORD
• Proofreading
• Line Edit (Copy-editing)
• Fix spelling and grammar
• Sales copy/summary revision
• $.04
• PER WORD
• Proofreading
• Organization and content
• Plot and pacing
• Manuscript Review
• $.06
• PER WORD
• Proofreading
• Plot and pacing
• Manuscript Review
• Formatting (print and ebook)
• Pre-publication proofread

```html
<!DOCTYPE html>
<html lang="en">
<head>
<meta charset="utf-8">
<title>Birch And Harbor – Book Editing</title>
<link href="https://fonts.googleapis.com/css2?family=Montserrat:wght@500;600;700;800&family=Open+Sans:wght@400;600;700&family=Roboto:wght@400;500;700&display=swap" rel="stylesheet">
<style>
:root{
  --red:#d9142b;
  --red-dark:#b50f22;
  --ink:#1b1b1b;
  --text:#555;
  --muted:#888;
  --ghost:#eeeeee;
  --line:#dddddd;
  --black:#0d0d0d;
  --white:#fff;
}
*{margin:0;padding:0;box-sizing:border-box}
html,body{width:1200px;height:3429px;overflow:hidden;background:var(--white)}
body{position:relative;font-family:"Open Sans",sans-serif;color:var(--text)}
.abs{position:absolute}

/* header */
.site-header{position:absolute;left:0;top:0;width:1200px;height:119px;background:var(--white);z-index:3}
.brand{position:absolute;left:98px;top:52px;display:flex;align-items:center;gap:8px;font-family:"Montserrat",sans-serif;font-weight:700;font-size:27px;color:var(--red)}
.brand-dot{width:14px;height:14px;border-radius:50%;background:var(--red)}
.main-nav{position:absolute;right:98px;top:52px;display:flex;gap:26px;align-items:center;font-family:"Roboto",sans-serif;font-weight:500;font-size:14px;color:var(--ink);letter-spacing:.2px}

/* hero */
.hero{position:absolute;left:0;top:119px;width:1200px;height:647px;overflow:hidden}
.hero-photo{position:absolute;inset:0;background:linear-gradient(120deg,#3a3a3a 0%,#8a8780 35%,#d9d4cb 60%,#6d6a63 85%,#2a2a2a 100%)}
.hero-shade{position:absolute;inset:0;background:rgba(0,0,0,.35)}
.hero-title{position:absolute;left:0;top:205px;width:1200px;text-align:center;font-family:"Montserrat",sans-serif;font-weight:800;font-size:46px;line-height:66px;color:var(--white);letter-spacing:1px}
.btn{display:inline-block;background:var(--red);color:var(--white);font-family:"Roboto",sans-serif;font-weight:700;text-transform:uppercase;border-radius:30px}
.hero-btn{position:absolute;left:502px;top:388px;width:196px;height:50px;line-height:50px;text-align:center;font-size:15px;letter-spacing:1px}
.hero-arrow{position:absolute;top:270px;width:30px;height:30px;border-radius:50%;background:rgba(0,0,0,.35)}
.hero-curve{position:absolute;left:0;bottom:0;width:1200px;height:140px}

/* process */
.ghost-word{position:absolute;font-family:"Montserrat",sans-serif;font-weight:800;color:var(--ghost);letter-spacing:2px}
.section-title{font-family:"Montserrat",sans-serif;font-weight:700;color:var(--ink);font-size:33px;letter-spacing:1px}
.process-title{position:absolute;left:98px;top:855px}
.process-intro{position:absolute;left:98px;top:922px;width:480px;font-size:13px;line-height:24px;color:var(--text)}
.check-list{list-style:none}
.check-list li{position:relative;padding-left:26px;font-size:13px;color:var(--text)}
.check-list li svg{position:absolute;left:0;top:50%;transform:translateY(-50%)}
.process-list{position:absolute;left:108px;top:1014px}
.process-list li{height:28px;line-height:28px}
.process-btn{position:absolute;left:98px;top:1182px;width:144px;height:45px;line-height:45px;text-align:center;font-size:12px}
.process-frame{position:absolute;left:697px;top:864px;width:457px;height:313px;border:3px solid var(--red)}
.process-photo{position:absolute;left:645px;top:923px;width:454px;height:302px;background:linear-gradient(135deg,#c9c4bc 0%,#8e8a84 40%,#4f5257 75%,#2f3236 100%);box-shadow:0 8px 20px rgba(0,0,0,.18)}
.divider{position:absolute;left:98px;top:1321px;width:1002px;height:1px;background:var(--line)}

/* pricing */
.pricing-title{position:absolute;left:0;top:1398px;width:1200px;text-align:center}
.pricing-sub{position:absolute;left:0;top:1465px;width:1200px;text-align:center;font-size:13px;line-height:26px;color:var(--text)}
.book{position:absolute;left:167px;top:1545px;width:866px;height:403px}
.book-page{position:absolute;top:0;width:433px;height:386px;background:var(--white);box-shadow:0 6px 22px rgba(0,0,0,.16)}
.book-page.left{left:0}
.book-page.right{left:433px;border-left:1px solid #e6e6e6}
.book-corner{position:absolute;top:0;width:30px;height:30px;border-top:3px solid var(--red)}
.book-corner.l{left:0;border-left:3px solid var(--red)}
.book-corner.r{right:0;border-right:3px solid var(--red)}
.page-num{position:absolute;top:20px;width:100%;text-align:center;font-size:12px;color:var(--ink)}
.plan-name{position:absolute;top:64px;width:100%;text-align:center;font-family:"Montserrat",sans-serif;font-weight:600;font-size:15px;letter-spacing:1px;color:var(--ink)}
.plan-price{position:absolute;top:116px;width:100%;text-align:center;font-family:"Montserrat",sans-serif;font-weight:700;font-size:56px;line-height:64px;color:var(--red)}
.plan-unit{position:absolute;top:182px;width:100%;text-align:center;font-family:"Montserrat",sans-serif;font-weight:700;font-size:37px;color:var(--red)}
.plan-note{position:absolute;top:258px;left:60px;width:313px;text-align:center;font-size:13px;line-height:26px;color:var(--ink)}
.page-mark{position:absolute;left:12px;top:40px;height:250px;writing-mode:vertical-rl;transform:rotate(180deg);font-family:"Montserrat",sans-serif;font-weight:700;font-size:20px;color:#f1d4d8}
.feature-title{position:absolute;left:110px;top:64px;font-family:"Montserrat",sans-serif;font-weight:700;font-size:17px;color:var(--ink)}
.feature-list{position:absolute;left:110px;top:109px}
.feature-list li{height:26.5px;line-height:26.5px;font-size:12px;color:var(--ink)}
.book-base{position:absolute;left:-4px;bottom:0;width:874px;height:30px}

/* services band */
.services{position:absolute;left:0;top:2041px;width:1200px;height:298px;background:linear-gradient(90deg,var(--red-dark),var(--red) 50%,var(--red-dark))}
.service{position:absolute;top:0;width:258px;text-align:center;color:var(--white)}
.service svg{position:absolute;left:96px;top:66px}
.service h3{position:absolute;top:154px;width:100%;font-family:"Roboto",sans-serif;font-weight:700;font-size:15px;letter-spacing:.3px}
.service p{position:absolute;top:186px;left:8px;width:242px;font-size:11px;line-height:22px;color:#ffe4e7}

/* news */
.news-title{position:absolute;left:0;top:2420px;width:1200px;text-align:center}
.news-sub{position:absolute;left:0;top:2482px;width:1200px;text-align:center;font-size:12px;color:var(--ink)}
.news-card{position:absolute;top:2540px;width:313px}
.news-photo{width:313px;height:190px}
.news-date{position:absolute;left:16px;top:16px;width:44px;height:52px;background:var(--red);color:var(--white);text-align:center;border-radius:3px;font-family:"Roboto",sans-serif}
.news-date small{display:block;font-size:10px;padding-top:5px}
.news-date b{display:block;font-size:17px;line-height:24px}
.news-card h4{margin-top:28px;font-family:"Roboto",sans-serif;font-weight:500;font-size:18px;line-height:27px;color:var(--ink)}
.news-meta{margin-top:14px;display:flex;align-items:center;gap:8px;font-size:12px;color:var(--muted)}
.news-meta i{width:1px;height:12px;background:#ccc;margin:0 6px}
.news-card p{margin-top:10px;font-size:12px;line-height:22px;color:var(--text)}

/* footer */
.footer-curve{position:absolute;left:0;top:2975px;width:1200px;height:80px}
.site-footer{position:absolute;left:0;top:3050px;width:1200px;height:379px;background:var(--black);color:var(--white)}
.footer-brand{position:absolute;left:0;top:30px;width:1200px;display:flex;justify-content:center;align-items:center;gap:8px;font-family:"Montserrat",sans-serif;font-weight:700;font-size:27px;color:var(--red)}
.footer-head{position:absolute;top:92px;font-family:"Roboto",sans-serif;font-weight:700;font-size:15px}
.contact-line{position:absolute;left:98px;display:flex;align-items:center;gap:16px;font-size:12px}
.subscribe-input{position:absolute;left:475px;top:132px;width:298px;height:39px;border:1px solid #bbb;padding-left:14px;line-height:37px;font-size:12px;color:var(--white)}
.subscribe-input svg{position:absolute;right:12px;top:13px}
.subscribe-btn{position:absolute;left:475px;top:187px;width:124px;height:34px;line-height:34px;text-align:center;font-size:12px}
.socials{position:absolute;left:928px;top:134px;display:flex;gap:14px}
.socials span{width:38px;height:38px;border-radius:50%;background:var(--white)}
.footer-rule{position:absolute;left:98px;top:269px;width:1002px;height:1px;background:#333}
.copyright{position:absolute;left:0;top:308px;width:1200px;text-align:center;font-size:12px}
</style>
</head>
<body>

<header class="site-header">
  <div class="brand"><span class="brand-dot"></span>Birch And Harbor</div>
  <nav class="main-nav">
    <span>HOME</span><span>ABOUT US</span><span>SERVICES</span><span>OUR PROCESS</span><span>PRICING</span><span>CONTACT</span>
    <svg width="14" height="14" viewBox="0 0 14 14"><circle cx="6" cy="6" r="4.5" fill="none" stroke="#1b1b1b" stroke-width="2"/><line x1="9.5" y1="9.5" x2="13" y2="13" stroke="#1b1b1b" stroke-width="2"/></svg>
  </nav>
</header>

<section class="hero">
  <div class="hero-photo" role="img" aria-label="Hands holding a manuscript at a bright writing desk"></div>
  <div class="hero-shade"></div>
  <svg class="hero-arrow" style="left:30px" viewBox="0 0 30 30"><path d="M18 9 L12 15 L18 21" fill="none" stroke="#fff" stroke-width="2"/></svg>
  <svg class="hero-arrow" style="right:30px" viewBox="0 0 30 30"><path d="M12 9 L18 15 L12 21" fill="none" stroke="#fff" stroke-width="2"/></svg>
  <h1 class="hero-title">NEED HELP PUBLISHING<br>A BESTSELLER?</h1>
  <span class="btn hero-btn">Contact Us</span>
  <svg class="abs" style="left:584px;top:544px" width="32" height="30" viewBox="0 0 32 30"><path d="M4 3 L16 13 L28 3 M4 15 L16 25 L28 15" fill="none" stroke="#fff" stroke-width="3"/></svg>
  <svg class="hero-curve" viewBox="0 0 1200 140" preserveAspectRatio="none">
    <path d="M0 40 Q560 175 1200 60 L1200 140 L0 140 Z" fill="#d9142b"/>
    <path d="M0 30 Q520 150 1200 75 L1200 140 L0 140 Z" fill="#fff"/>
    <path d="M0 30 Q420 128 1200 112 L1200 140 L0 140 Z" fill="#fff"/>
  </svg>
</section>

<div class="ghost-word" style="left:6px;top:890px;font-size:56px;writing-mode:vertical-rl;transform:rotate(180deg)">PROCESS</div>
<h2 class="section-title process-title">OUR PROCESS</h2>
<p class="process-intro">Send us a sample of your book. Our caffeine-fueled, eagle-eyed editors will go through it and then email you with their comments and suggestions. You can ask them any questions you want. They will look for...</p>
<ul class="check-list process-list">
  <li><svg width="14" height="14" viewBox="0 0 14 14"><path d="M2 12 L12 2 M3 8 L6 11" stroke="#d9142b" stroke-width="2"/></svg>Typos and grammatical errors.</li>
  <li><svg width="14" height="14" viewBox="0 0 14 14"><path d="M2 12 L12 2 M3 8 L6 11" stroke="#d9142b" stroke-width="2"/></svg>Spelling and word choice issues</li>
  <li><svg width="14" height="14" viewBox="0 0 14 14"><path d="M2 12 L12 2 M3 8 L6 11" stroke="#d9142b" stroke-width="2"/></svg>Punctuation and style</li>
  <li><svg width="14" height="14" viewBox="0 0 14 14"><path d="M2 12 L12 2 M3 8 L6 11" stroke="#d9142b" stroke-width="2"/></svg>Word choice, clarity and flow.</li>
  <li><svg width="14" height="14" viewBox="0 0 14 14"><path d="M2 12 L12 2 M3 8 L6 11" stroke="#d9142b" stroke-width="2"/></svg>Sentence structure and craft</li>
</ul>
<span class="btn process-btn">Read More &#10148;</span>
<div class="process-frame"></div>
<div class="process-photo" role="img" aria-label="Editor reviewing a manuscript at a desktop computer in an office"></div>
<div class="divider"></div>

<div class="ghost-word" style="left:0;top:1380px;width:1200px;text-align:center;font-size:60px">OUR PACKAGES</div>
<h2 class="section-title pricing-title">OUR PRICING</h2>
<p class="pricing-sub">Our proofreading, editing and manuscript review packages are specifically tailored to help you<br>publish the best possible version of your story.</p>

<div class="book">
  <div class="book-page left">
    <span class="book-corner l"></span>
    <span class="page-num">3</span>
    <div class="plan-name">ADVANCED PLAN</div>
    <div class="plan-price">$.04</div>
    <div class="plan-unit">PER WORD</div>
    <p class="plan-note">We've carefully structured our packages to maximize value for every budget.</p>
  </div>
  <div class="book-page right">
    <span class="book-corner r"></span>
    <span class="page-num">4</span>
    <div class="page-mark">Birch And Harbor</div>
    <div class="feature-title">PER WORD</div>
    <ul class="check-list feature-list">
      <li><svg width="14" height="14" viewBox="0 0 14 14"><path d="M2 12 L12 2 M3 8 L6 11" stroke="#d9142b" stroke-width="2"/></svg>Proofreading</li>
      <li><svg width="14" height="14" viewBox="0 0 14 14"><path d="M2 12 L12 2 M3 8 L6 11" stroke="#d9142b" stroke-width="2"/></svg>Line Edit (Copy-editing)</li>
      <li><svg width="14" height="14" viewBox="0 0 14 14"><path d="M2 12 L12 2 M3 8 L6 11" stroke="#d9142b" stroke-width="2"/></svg>Fix spelling and grammar</li>
      <li><svg width="14" height="14" viewBox="0 0 14 14"><path d="M2 12 L12 2 M3 8 L6 11" stroke="#d9142b" stroke-width="2"/></svg>Sales copy or summary revision</li>
      <li><svg width="14" height="14" viewBox="0 0 14 14"><path d="M2 12 L12 2 M3 8 L6 11" stroke="#d9142b" stroke-width="2"/></svg>Organization and content</li>
      <li><svg width="14" height="14" viewBox="0 0 14 14"><path d="M2 12 L12 2 M3 8 L6 11" stroke="#d9142b" stroke-width="2"/></svg>Plot and pacing</li>
      <li><svg width="14" height="14" viewBox="0 0 14 14"><path d="M2 12 L12 2 M3 8 L6 11" stroke="#d9142b" stroke-width="2"/></svg>Manuscript Review</li>
    </ul>
  </div>
  <svg class="book-base" viewBox="0 0 874 30" preserveAspectRatio="none">
    <path d="M0 0 Q220 14 437 8 Q654 14 874 0 L874 14 Q654 30 437 22 Q220 30 0 14 Z" fill="#9a9a9a"/>
  </svg>
</div>

<section class="services">
  <div class="service" style="left:70px">
    <svg width="66" height="66" viewBox="0 0 66 66" fill="none" stroke="#fff" stroke-width="2.5"><rect x="8" y="14" width="12" height="44"/><rect x="22" y="8" width="12" height="50"/><circle cx="46" cy="30" r="10"/><line x1="52" y1="38" x2="60" y2="56"/></svg>
    <h3>PROOFREADING</h3>
    <p>Nemo enim ipsam voluptam quia voluptas sit aspernatur aut odit aut fugit</p>
  </div>
  <div class="service" style="left:340px">
    <svg width="66" height="66" viewBox="0 0 66 66" fill="none" stroke="#fff" stroke-width="2.5"><rect x="6" y="10" width="54" height="38"/><line x1="14" y1="20" x2="40" y2="20"/><line x1="14" y1="28" x2="52" y2="28"/><line x1="14" y1="36" x2="46" y2="36"/><path d="M24 48 L20 58 H46 L42 48"/></svg>
    <h3>CONTENT EDITING</h3>
    <p>Nemo enim ipsam voluptam quia voluptas sit aspernatur aut odit aut fugit</p>
  </div>
  <div class="service" style="left:600px">
    <svg width="66" height="66" viewBox="0 0 66 66" fill="none" stroke="#fff" stroke-width="2.5"><path d="M33 6 L36 13 L43 13 L37 18 L39 25 L33 21 L27 25 L29 18 L23 13 L30 13 Z"/><circle cx="12" cy="20" r="5"/><circle cx="54" cy="20" r="5"/><rect x="8" y="34" width="22" height="24"/><path d="M36 58 V40 H44 L48 32 H56 V58 Z"/></svg>
    <h3>MANUSCRIPT REVIEW</h3>
    <p>Nemo enim ipsam voluptam quia voluptas sit aspernatur aut odit aut fugit</p>
  </div>
  <div class="service" style="left:860px">
    <svg width="66" height="66" viewBox="0 0 66 66" fill="none" stroke="#fff" stroke-width="2.5"><rect x="18" y="6" width="36" height="44"/><path d="M18 12 H12 V56 H48 V50"/><line x1="26" y1="18" x2="46" y2="18"/><line x1="26" y1="26" x2="46" y2="26"/><line x1="26" y1="34" x2="40" y2="34"/></svg>
    <h3>BOOK BUILDING</h3>
    <p>Nemo enim ipsam voluptam quia voluptas sit aspernatur aut odit aut fugit</p>
  </div>
</section>

<div class="ghost-word" style="left:0;top:2402px;width:1200px;text-align:center;font-size:64px">LATEST NEWS</div>
<h2 class="section-title news-title">LATEST NEWS</h2>
<p class="news-sub">Read The Latest News Regarding Our Book Editing Company.</p>

<article class="news-card" style="left:98px">
  <div class="news-photo" role="img" aria-label="Fountain pen resting on an open book" style="background:linear-gradient(135deg,#1f5a2c,#2e7d3a 50%,#b89a6a)"></div>
  <div class="news-date"><small>June</small><b>12</b></div>
  <h4>Minus id quod maxime placeat Facere possimus</h4>
  <div class="news-meta">&#9679; Maren <i></i> &#9993; 214 Comments</div>
  <p>Nam libero tempore, cum soluta nobis est eligendi optio cumque nihil impedit quo minus</p>
</article>
<article class="news-card" style="left:443px">
  <div class="news-photo" role="img" aria-label="Writer working on a laptop at a desk" style="background:linear-gradient(135deg,#d7cdbf,#a48a6c 50%,#5b4a3a)"></div>
  <div class="news-date"><small>June</small><b>12</b></div>
  <h4>Minus id quod maxime placeat Facere possimus</h4>
  <div class="news-meta">&#9679; Maren <i></i> &#9993; 214 Comments</div>
  <p>Nam libero tempore, cum soluta nobis est eligendi optio cumque nihil impedit quo minus</p>
</article>
<article class="news-card" style="left:788px">
  <div class="news-photo" role="img" aria-label="Hand writing notes with a pen on paper" style="background:linear-gradient(135deg,#eef2f6,#b9c6d3 50%,#5d7288)"></div>
  <div class="news-date"><small>June</small><b>12</b></div>
  <h4>Minus id quod maxime placeat Facere possimus</h4>
  <div class="news-meta">&#9679; Maren <i></i> &#9993; 214 Comments</div>
  <p>Nam libero tempore, cum soluta nobis est eligendi optio cumque nihil impedit quo minus</p>
</article>

<svg class="footer-curve" viewBox="0 0 1200 80" preserveAspectRatio="none">
  <path d="M0 75 Q600 -10 1200 75 L1200 80 L0 80 Z" fill="#d9142b"/>
  <path d="M0 80 Q600 12 1200 80 Z" fill="#0d0d0d"/>
</svg>
<footer class="site-footer">
  <div class="footer-brand"><span class="brand-dot"></span>Birch And Harbor</div>
  <div class="footer-head" style="left:98px">Contact Us</div>
  <div class="contact-line" style="top:146px">
    <svg width="14" height="14" viewBox="0 0 14 14"><path d="M2 1 L5 1 L6 4 L4 5.5 Q5.5 8.5 8.5 10 L10 8 L13 9 L13 12 Q6 13 1 4 Z" fill="#fff"/></svg>(+1) 555 014 2290</div>
  <div class="contact-line" style="top:189px">
    <svg width="14" height="12" viewBox="0 0 14 12"><rect x="0" y="0" width="14" height="12" fill="#fff"/><path d="M0 0 L7 6 L14 0" fill="none" stroke="#0d0d0d" stroke-width="1.5"/></svg>hello@birchandharbor.com</div>
  <div class="footer-head" style="left:475px">Newsletter Subscribe</div>
  <div class="subscribe-input">Enter Email
    <svg width="14" height="12" viewBox="0 0 14 12"><rect width="14" height="12" fill="#fff"/><path d="M0 0 L7 6 L14 0" fill="none" stroke="#0d0d0d" stroke-width="1.5"/></svg>
  </div>
  <span class="btn subscribe-btn">Subscribe</span>
  <div class="footer-head" style="left:928px">Follow Us On</div>
  <div class="socials"><span></span><span></span><span></span><span></span></div>
  <div class="footer-rule"></div>
  <p class="copyright">Copyrights © 2018 Birch And Harbor.  All Rights Reserved.</p>
</footer>

</body>
</html>
```